Catering Menu Package

I currently have a complete menu package, which we have redesigned as far as content, now I need to it put together in a catalog type format. It is essentially 10-12 pages in length, and will be sent for print production. Upon receiving a final edit
Updates

I have added an example gif to the project.

I did this free hand this basically what I am looking for. please change text and type to whatever you think would look best. This is a total rough design so, feel free to change any and everything. The text for the page is on the word documents. If you need more images let me know I am in the process of getting as many images uploaded for your use.

Project Deadline Extended
Reason: I figured we got a late jump with questions, so i am extending a few days .

Target Market(s)

The target market is business who wish to have catered luncheons, breakfasts , meetings

Industry/Entity Type

Catering

Requirements
Must have
• I have attached a copy of the text that what we want in the package, our logo, and i have also attached a catering package of another company to give you an idea what the finished product will be
Should not have
• It should not look identical to the example catering packages, these are for some inspiration we want our own design with the same type of look and feel

```html
<!DOCTYPE html>
<html lang="en">
<head>
<meta charset="utf-8">
<title>Hot Entrées — Harbor Lane Caterers</title>
<link href="https://fonts.googleapis.com/css2?family=Lora:ital,wght@0,400;0,700;1,400;1,700&family=Pinyon+Script&display=swap" rel="stylesheet">
<style>
  :root {
    --page: #ffffff;
    --sidebar-top: #ffffff;
    --sidebar-bottom: #e6dad2;
    --panel-top: #ffffff;
    --panel-bottom: #f3f1f0;
    --accent: #d6453f;
    --body: #5b4a42;
    --heading: #6f6560;
    --ink: #1e1a18;
  }
  html, body {
    margin: 0;
    padding: 0;
    width: 1200px;
    height: 927px;
    overflow: hidden;
    background: var(--page);
  }
  .menu-page {
    position: relative;
    width: 1200px;
    height: 927px;
    overflow: hidden;
    font-family: "Lora", Georgia, serif;
    color: var(--body);
  }
  .sidebar {
    position: absolute;
    left: 0; top: 0;
    width: 183px; height: 927px;
    background: linear-gradient(180deg, var(--sidebar-top) 0%, var(--sidebar-top) 35%, var(--sidebar-bottom) 100%);
  }
  .panel {
    position: absolute;
    left: 183px; top: 0;
    width: 1017px; height: 927px;
    background: linear-gradient(135deg, var(--panel-top) 30%, var(--panel-bottom) 100%);
  }
  .brand {
    position: absolute;
    left: 28px; top: 60px;
    width: 132px;
    text-align: center;
  }
  .brand-mark {
    display: block;
    width: 60px; height: 60px;
    margin: 0 auto 16px;
    border: 3px solid var(--ink);
    box-sizing: border-box;
  }
  .brand-name {
    margin: 0;
    font-size: 22px;
    font-weight: 700;
    line-height: 1.15;
    color: var(--ink);
    text-transform: lowercase;
  }
  .section-title {
    position: absolute;
    left: 198px; top: 42px;
    margin: 0;
    font-family: "Pinyon Script", cursive;
    font-weight: 400;
    font-size: 44px;
    color: var(--heading);
  }
  .entree {
    position: absolute;
    margin: 0;
  }
  .entree--left { left: 197px; width: 450px; }
  .entree--right { left: 692px; width: 475px; }
  .entree-name {
    margin: 0 0 2px;
    font-size: 19px;
    font-style: italic;
    font-weight: 700;
    color: var(--accent);
    line-height: 26px;
  }
  .entree-desc, .entree-addon {
    margin: 0;
    font-size: 17px;
    line-height: 24px;
  }
  .entree-addon { font-style: italic; }
  .price { margin-left: 14px; white-space: nowrap; }
</style>
</head>
<body>
<main class="menu-page">
  <div class="sidebar"></div>
  <div class="panel"></div>

  <div class="brand">
    <span class="brand-mark"></span>
    <p class="brand-name">Harbor<br>Lane<br>Caterers</p>
  </div>

  <h1 class="section-title">Hot Entrées</h1>

  <article class="entree entree--left" style="top:124px">
    <h2 class="entree-name">Chesapeake Crab Cake</h2>
    <p class="entree-desc">6oz Jumbo Lump Crab Cake served with House-made Remoulade Oven Roasted Redskin Potatoes, &amp; Sautéed Local Corn.<span class="price">$&amp;.&amp;&amp;</span></p>
  </article>

  <article class="entree entree--left" style="top:245px">
    <h2 class="entree-name">Key West Grilled Salmon</h2>
    <p class="entree-desc">Served with Pina-Colada Jeweled Rice, Fire-Roasted Seasonal Vegetable Medley, &amp; Fresh Mango Salsa.<br>$&amp;.&amp;&amp;</p>
  </article>

  <article class="entree entree--left" style="top:366px">
    <h2 class="entree-name">Tropical Grilled Chicken</h2>
    <p class="entree-desc">Jamaican Jerk Rubbed Chicken Breast grilled &amp; topped with Fresh Mango Salsa, served with Roasted Seasonal Vegetable Medley, Jeweled Jasmine Rice, Pineapple Hawaiian Cole Slaw.<span class="price">$&amp;.&amp;&amp;</span></p>
    <p class="entree-addon">Add Cilantro, Grilled Mahi-Mahi &amp; Fresh Mango Salsa<br>$&amp;.&amp;&amp;</p>
  </article>

  <article class="entree entree--left" style="top:560px">
    <h2 class="entree-name">Fried Chicken Picnic</h2>
    <p class="entree-desc">Country Fried 8-cut Chicken served with Potato Salad, Pasta-Vegetable Salad, Creamy Cole Slaw, &amp; Fresh Watermelon Wedge.<span class="price">$&amp;.&amp;&amp;</span></p>
  </article>

  <article class="entree entree--left" style="top:681px">
    <h2 class="entree-name">Chicken Parmesan</h2>
    <p class="entree-desc">Lightly Breaded Chicken Breast, golden fried, &amp; topped with Chef-crafted Marinara, Melted Provolone &amp; Mozzarella, &amp; served with Penne Pasta.<span class="price">$&amp;.&amp;&amp;</span></p>
  </article>

  <article class="entree entree--right" style="top:176px">
    <h2 class="entree-name">Chef-Made Italian Sausage Lasagna</h2>
    <p class="entree-desc">Fresh Pasta, stacked high &amp; layered with Ricotta, Italian Sausage, House Made Marinara &amp; Provolone &amp; Mozzarella Cheeses.<span class="price">$&amp;.&amp;&amp;</span></p>
  </article>

  <article class="entree entree--right" style="top:296px">
    <h2 class="entree-name">Fajita Lunch</h2>
    <p class="entree-desc">Your choice of grilled Chicken breast strips or grilled Sirloin Steak strips, with Fire-Roasted Peppers &amp; Onions, Flour Tortillas, Cuban Stewed Black Beans, Spanish Rice, &amp; Fire-Roasted Seasonal Vegetable Medley. Diced Tomatoes, Salsa, Sour Cream, Crisp Lettuce, Shredded Cheese, &amp; Jalapeño Garni.<span class="price">$&amp;.&amp;&amp;</span></p>
    <p class="entree-addon">Make it a Chicken &amp; Beef Combo<span class="price">$&amp;.&amp;&amp;</span><br>Add Fresh Made Guacamole<span class="price">$&amp;.&amp;&amp;</span></p>
  </article>

  <article class="entree entree--right" style="top:538px">
    <h2 class="entree-name">Ragn’ Cajun Lunch</h2>
    <p class="entree-desc">Cajun Rubbed &amp; Bourbon Sauce Basted 8-cut Chicken Served with Red Beans &amp; Rice &amp; Lemon Scented Petit Green Beans.<span class="price">$&amp;.&amp;&amp;</span></p>
  </article>

  <article class="entree entree--right" style="top:659px">
    <h2 class="entree-name">Grilled Vegetable Lasagna</h2>
    <p class="entree-desc">Fresh Pasta, stacked high &amp; layered with Ricotta, Grilled Seasonal Vegetables, House Made Marinara, &amp; Provolone &amp; Mozzarella Cheeses.<span class="price">$&amp;.&amp;&amp;</span></p>
  </article>

  <article class="entree entree--right" style="top:780px">
    <h2 class="entree-name">Three Cheese Stuffed Shells</h2>
    <p class="entree-desc">Served over Chef-Crafted Marinara with Balsamic Roasted Seasonal Vegetable Medley.<span class="price">$&amp;.&amp;&amp;</span></p>
  </article>
</main>
</body>
</html>
```